GJ & DW Fencing Pty Ltd

We already have an existing logo created by Pixel Harbour however we have restructured to a company. We would like someone to add Pty Ltd to our business name please.

Colors

Designer to choose only greyscale colors for use in the design.

```html
<!DOCTYPE html>
<html lang="en">
<head>
<meta charset="utf-8">
<title>GJ &amp; DW Fencing Pty Ltd — Business Card</title>
<link href="https://fonts.googleapis.com/css2?family=Noto+Serif:wght@700&family=Lato:wght@400&display=swap" rel="stylesheet">
<style>
  :root {
    --backdrop: #666666;
    --card-light: #ffffff;
    --card-dark: #0b0b0b;
    --ink: #111111;
    --ink-inverse: #ffffff;
    --fleece-light: #eeeeee;
    --fleece-mid: #cfcfcf;
  }
  * { margin: 0; padding: 0; box-sizing: border-box; }
  html, body {
    width: 1200px; height: 900px; overflow: hidden;
    background: var(--backdrop);
  }
  .canvas { position: relative; width: 1200px; height: 900px; }

  .card {
    position: absolute; top: 200px; width: 310px; height: 502px;
  }
  .card--front {
    left: 253px; background: var(--card-light);
    border-radius: 50px 0 50px 0;
  }
  .card--back {
    left: 627px; background: var(--card-dark);
    border-radius: 0 50px 0 50px;
  }

  .brand-name {
    position: absolute; left: 39px; top: 120px; width: 230px;
    font-family: "Noto Serif", Georgia, serif; font-weight: 700;
    color: var(--ink); text-align: center; line-height: 1;
  }
  .brand-name__main { display: block; font-size: 38px; letter-spacing: 0.5px; }
  .brand-name__sub { display: block; font-size: 17px; letter-spacing: 1px; margin-top: 8px; }

  .holder-name {
    position: absolute; left: 33px; top: 322px;
    font-family: "Noto Serif", Georgia, serif; font-weight: 700;
    font-size: 17px; color: var(--ink); letter-spacing: 0.3px;
  }

  .contact-list {
    position: absolute; left: 33px; top: 370px; list-style: none;
    font-family: "Lato", Arial, sans-serif; font-size: 14px; color: var(--ink);
  }
  .contact-list__item { display: flex; align-items: center; height: 22px; }
  .contact-list__item--address { margin-top: 12px; }
  .contact-list__icon { width: 21px; height: 21px; margin-right: 7px; flex: none; }

  .fleece-figure {
    position: absolute; left: 23px; top: 75px; width: 265px; height: 350px;
    border-radius: 42% 46% 20% 20% / 30% 30% 12% 12%;
    background: radial-gradient(ellipse at 50% 40%, var(--fleece-light) 0%, var(--fleece-mid) 100%);
  }
</style>
</head>
<body>
<main class="canvas">
  <section class="card card--front" aria-label="Card front">
    <h1 class="brand-name">
      <span class="brand-name__main">GJ &amp; DW</span>
      <span class="brand-name__sub">FENCING PTY LTD</span>
    </h1>

    <p class="holder-name">DALE WHITFORD</p>

    <ul class="contact-list">
      <li class="contact-list__item">
        <svg class="contact-list__icon" viewBox="0 0 24 24" aria-hidden="true">
          <circle cx="12" cy="12" r="12" fill="#111"/>
          <path d="M8.2 6.5l2 2.4-1.2 1.5c.8 1.7 2 2.9 3.6 3.7l1.5-1.2 2.4 2-1.1 2.1c-4.3-.3-8-4-8.3-8.3z" fill="#fff"/>
        </svg>
        048 5129374
      </li>
      <li class="contact-list__item">
        <svg class="contact-list__icon" viewBox="0 0 24 24" aria-hidden="true">
          <circle cx="12" cy="12" r="12" fill="#111"/>
          <rect x="6" y="8" width="12" height="8.5" rx="1" fill="#fff"/>
          <path d="M6.5 8.6L12 13l5.5-4.4" fill="none" stroke="#111" stroke-width="1.2"/>
        </svg>
        gjdwfencing@mailbox.com
      </li>
      <li class="contact-list__item contact-list__item--address">
        <svg class="contact-list__icon" viewBox="0 0 24 24" aria-hidden="true">
          <circle cx="12" cy="12" r="12" fill="#111"/>
          <path d="M12 5a4.6 4.6 0 0 0-4.6 4.6c0 3.4 4.6 8.6 4.6 8.6s4.6-5.2 4.6-8.6A4.6 4.6 0 0 0 12 5z" fill="#fff"/>
          <circle cx="12" cy="9.6" r="1.8" fill="#111"/>
        </svg>
        PO Box 418 Merredin WA 6415
      </li>
    </ul>
  </section>

  <section class="card card--back" aria-label="Card back">
    <div class="fleece-figure" role="img" aria-label="Large white textured illustration of a standing sheep"></div>
  </section>
</main>
</body>
</html>
```